Catalogue Design Project

We need a catalog design for a new private university called Redwell Institute Bayshore (see website www.rwi-bs.org). The catalog should be about 30 pages maximum and will include items such as General Information, Academic schedule, department descriptions, program descriptions, course descriptions, school policies, student services, admissions, San diego Lifestyle, etc.
I will provide the text but I need a professional design with regard to page layouts. I have provided some examples.
Ok, i posted the catalog content, just missing course descriptions.
Target Market(s)
Young Professionals, Foreign Students
Industry/Entity Type
University
Look and feel
Each slider illustrates characteristics of the customer's brand and the style your logo design should communicate.

```html
<!DOCTYPE html>
<html lang="en">
<head>
<meta charset="utf-8">
<title>Online Learning — Redwell Institute Bayshore Catalog</title>
<link rel="stylesheet" href="https://fonts.googleapis.com/css2?family=Carlito:wght@400;700&display=swap">
<style>
  :root {
    --ink: #1d1d1d;
    --brand-blue: #2f5f8f;
    --rule-blue: #5d86b0;
    --rule-grey: #b9c3cc;
    --footer-grey: #8a8f94;
    --paper: #ffffff;
  }
  * { margin: 0; padding: 0; box-sizing: border-box; }
  html, body { width: 927px; height: 1200px; overflow: hidden; background: var(--paper); }
  body { font-family: "Carlito", "Calibri", sans-serif; color: var(--ink); }
  .page { position: relative; width: 927px; height: 1200px; }

  .dot-mark {
    position: absolute; left: 60px; top: 36px; width: 154px; height: 34px;
    border-radius: 17px;
    background: linear-gradient(90deg, #9ea4aa 0%, #a9aeb4 70%, #3f6e9c 100%);
    opacity: .75;
  }
  .header-photo {
    position: absolute; right: 0; top: 0; width: 370px; height: 103px;
    background: linear-gradient(90deg, rgba(255,255,255,1) 0%, #ece4d6 35%, #cdbb9b 70%, #b59a73 100%);
  }
  .header-rule {
    position: absolute; left: 0; top: 101px; width: 927px; height: 2px;
    background: var(--rule-blue);
  }
  .section-tab {
    position: absolute; right: 0; top: 103px; width: 336px; height: 38px;
    background: var(--brand-blue);
    color: #fff; font-size: 29px; letter-spacing: .5px;
    display: flex; align-items: center; padding-left: 42px;
    clip-path: polygon(0 0, 100% 0, 100% 100%, 22px 100%);
  }
  .page-title {
    position: absolute; left: 0; width: 927px; top: 186px;
    text-align: center; font-size: 26px; font-weight: 700;
  }
  .hero {
    position: absolute; left: 67px; top: 232px; width: 795px; height: 401px;
    background:
      radial-gradient(circle at 50% 40%, rgba(255,236,200,.9) 0%, rgba(255,236,200,0) 35%),
      linear-gradient(90deg, #6f7f9a 0%, #c8b6c8 40%, #e7d9e3 60%, #a9b2c2 100%);
  }
  .body-copy {
    position: absolute; left: 76px; top: 650px; width: 786px;
    font-size: 17.6px; line-height: 37px; text-align: justify;
  }
  .body-copy p + p { margin-top: 37px; }
  .footer-rule {
    position: absolute; left: 0; top: 1158px; width: 927px; height: 2px;
    background: var(--rule-grey);
  }
  .folio {
    position: absolute; right: 38px; top: 1170px;
    font-size: 12.5px; color: var(--footer-grey); letter-spacing: .3px;
  }
</style>
</head>
<body>
<div class="page">
  <div class="dot-mark" role="img" aria-label="Decorative pattern of grey and blue dots"></div>
  <div class="header-photo" role="img" aria-label="Photograph of an open antique book fading into white"></div>
  <div class="header-rule"></div>
  <div class="section-tab">ONLINE LEARNING</div>

  <h1 class="page-title">Online Learning</h1>

  <div class="hero" role="img" aria-label="Collage of students studying on computers with a keyboard and soft cloud overlay"></div>

  <div class="body-copy">
    <p>RWIB offers students the option of taking coursework online through our Redwell Virtual Education (REVE) network. Simply select the course you would like to take, the session, and then login to REVE to get started. It's never been easier to take classes and receive school credit from the comfort of your home, office or other available internet location. RWIB's virtual campus offers students the most technologically advanced educational tools available online including, but not limited to self-guiding tutorials for lectures, lesson plans and homework assignments, graphically-rich presentations, videos, live broadcasts from instructors and classmates, quick teacher feedback, application-loaded discussion boards, online sample exams with scores and analysis of strengths and weaknesses, progress reports and many others.</p>
    <p>Please see the current schedule for online class availability.</p>
  </div>

  <div class="footer-rule"></div>
  <div class="folio">19::: REDWELL INSTITUTE</div>
</div>
</body>
</html>
```